Concierge Dental / Medical Supply Ordering Business - Sleek, Efficient, Professional, Elite

www.brantonkeelmedical.com - example website.

We are a concierge supply ordering business for medical and dental that provide DSO price savings on supplies while maintaining business autonomy and independence.

We want a very simple website that looks very professional says what we do and gives a very simple method to contact us & sign up as above.

Target Market(s)

Independent Dental and Medical Practices

Industry/Entity Type

Dental and Medical - healthcare

Coding

Coded - Design and coding required

Number of Pages Required

3 page

Font styles to use
Sans Serif

Colors
0054AA
0677BA
7BADD7
CADEEF
E8F1F8

Requirements
Must have
• Simple contact page, sleek efficient design, uncomplicated.
Nice to have
• Sign up page vs just a contact page.
Should not have
• Lots of pages, hard to navigate,

```html
<!DOCTYPE html>
<html lang="en">
<head>
<meta charset="utf-8">
<title>Clearpoint Dental Supply</title>
<link href="https://fonts.googleapis.com/css2?family=Lato:wght@400;700;900&display=swap" rel="stylesheet">
<style>
:root{
  --accent:#10a8e8;
  --navy:#0f4a7a;
  --ink:#111111;
  --text:#2a2a2a;
  --muted:#8a8a8a;
  --light:#f2f2f2;
  --ring:#8d8e91;
  --footer:#161616;
  --white:#ffffff;
  --star:#f5a623;
}
*{box-sizing:border-box;margin:0;padding:0}
html,body{width:1200px;height:3686px;overflow:hidden}
body{position:relative;font-family:'Lato',sans-serif;color:var(--text);background:var(--white)}
.abs{position:absolute}
.btn{position:absolute;display:flex;align-items:center;justify-content:center;background:var(--accent);color:var(--white);font-weight:700;font-size:17px;border-radius:4px;box-shadow:0 3px 8px rgba(0,0,0,.18)}
.mark-square{position:absolute;background:linear-gradient(135deg,#c9ccd1,#6f86a8);border-radius:4px}
.section-title{position:absolute;font-weight:700;font-size:37px;color:var(--ink)}
.section-title span{color:var(--accent)}

/* hero */
.hero-ring{left:0;top:0;width:1200px;height:646px;background:var(--ring);border-radius:0 0 110px 110px}
.hero{left:0;top:0;width:1200px;height:630px;border-radius:0 0 100px 100px;overflow:hidden;
  background:linear-gradient(100deg,#3e4448 0%,#6d7377 35%,#a9b0b5 60%,#d7dcdf 80%,#c3c8cc 100%)}
.nav-band{left:0;top:0;width:1200px;height:85px;background:rgba(60,62,66,.72)}
.brand-badge{left:107px;top:-22px;width:176px;height:176px;border-radius:50%;background:#3b3d40;display:flex;align-items:center;justify-content:center;padding-top:40px}
.brand-name{color:var(--white);font-weight:700;font-size:14px}
.nav{top:31px;color:var(--white);font-size:15px}
.nav-cta{left:972px;top:20px;width:115px;height:42px;font-size:15px}
.hero-kicker{left:112px;top:244px;color:var(--white);font-size:21px;font-weight:700}
.hero-title{left:112px;top:282px;color:var(--white);font-size:44px;font-weight:700}
.hero-copy{left:112px;top:350px;width:400px;color:var(--white);font-size:14.5px;line-height:27.5px}
.hero-btn{left:112px;top:453px;width:131px;height:46px;background:var(--white);color:var(--accent)}

/* about */
.about-visual{left:132px;top:740px;width:350px;height:340px;border-radius:48px;background:linear-gradient(135deg,#eef1f4,#b9c3cf);display:flex;align-items:center;justify-content:center;font-weight:700;font-size:22px;color:var(--navy)}
.about-copy{left:545px;width:550px;font-size:14.5px;line-height:29.3px}

/* areas */
.areas{left:0;top:1163px;width:1200px;height:742px;background:var(--navy);border-radius:70px}
.rule{position:absolute;left:112px;width:977px;height:1px;background:rgba(255,255,255,.55)}
.area-img{position:absolute;left:112px;width:214px;height:86px}
.area-name{position:absolute;left:431px;color:var(--white);font-weight:700;font-size:20px}
.area-desc{position:absolute;left:683px;width:410px;color:var(--white);font-size:13.5px;line-height:26.5px}

/* testimonials */
.card{position:absolute;width:312px;height:340px;background:var(--white);padding:28px 17px 0}
.card.outlined{border:1.5px solid #4db3e6}
.card.raised{box-shadow:0 0 24px rgba(16,168,232,.2);height:337px}
.stars{color:var(--star);font-size:19px;letter-spacing:1px}
.quote{margin-top:18px;font-size:14.5px;line-height:27.5px;color:var(--text)}
.person{position:absolute;left:17px;bottom:20px;display:flex;align-items:center;gap:14px}
.avatar{width:64px;height:64px;border-radius:50%;background:linear-gradient(135deg,#b7b2ab,#6a6460)}
.person-name{font-weight:700;font-size:15px;color:var(--ink)}
.person-loc{font-size:13.5px;color:var(--muted);margin-top:4px}

/* contact */
.contact{left:0;top:2548px;width:1200px;height:720px;background:var(--light);border-radius:110px 110px 0 0}
.field{position:absolute;border:1.5px solid #2d5f9e;background:var(--white);padding:0 22px;font-weight:700;font-size:15px;color:var(--ink);display:flex;align-items:center}
.field.area{align-items:flex-start;padding-top:26px}

/* footer */
.footer-arc{left:0;top:3222px;width:1200px;height:464px;background:var(--accent);border-radius:220px 220px 0 0}
.footer{left:0;top:3242px;width:1200px;height:444px;background:var(--footer);border-radius:210px 210px 0 0}
.foot-brand{left:133px;top:3345px;width:210px;text-align:center}
.foot-brand .mark-square{position:static;display:block;width:120px;height:120px;margin:0 auto 20px;border-radius:20px}
.foot-brand p{color:var(--white);font-weight:700;font-size:20px}
.foot-head{top:3343px;color:var(--white);font-weight:700;font-size:20px}
.foot-list{list-style:none;color:var(--white);font-size:15px}
.foot-list li{height:34px;display:flex;align-items:center;gap:10px}
.foot-contact{color:var(--white);font-size:15px;line-height:27px}
.ic{width:32px;height:32px;border-radius:50%;background:var(--accent);display:flex;align-items:center;justify-content:center;position:absolute}
.foot-rule{left:112px;top:3592px;width:977px;height:1px;background:#8a8a8a}
.copy{left:113px;top:3629px;color:var(--white);font-size:15px}
.social{position:absolute;top:3627px;width:26px;height:26px;border-radius:50%;background:#1a7fd6}
</style>
</head>
<body>

<!-- hero -->
<div class="abs hero-ring"></div>
<div class="abs hero" role="img" aria-label="Photo of a dentist in mask and safety glasses treating a smiling patient in a bright clinic"></div>
<div class="abs nav-band"></div>
<div class="abs brand-badge"><span class="brand-name">ClearpointDentalSupply</span></div>
<span class="abs nav" style="left:430px">Home</span>
<span class="abs nav" style="left:519px">About</span>
<span class="abs nav" style="left:609px">Areas of Practice</span>
<span class="abs nav" style="left:771px">Why Choose Us</span>
<svg class="abs" style="left:919px;top:35px" width="14" height="14" viewBox="0 0 14 14"><circle cx="6" cy="6" r="4.5" fill="none" stroke="#fff" stroke-width="2"/><line x1="9.3" y1="9.3" x2="13" y2="13" stroke="#fff" stroke-width="2"/></svg>
<div class="btn nav-cta">Contact Us</div>
<p class="abs hero-kicker">Welcome to</p>
<h1 class="abs hero-title">Clearpoint Dental Supply</h1>
<p class="abs hero-copy">Itaque earum rerum hic tenetur a sapiente delectus, ut aut reiciendis voluptatibus maiores alias consequatur aut perferendis doloribus asperiores repellat.</p>
<div class="btn hero-btn">Get Started</div>

<!-- about -->
<div class="abs about-visual">Clearpoint</div>
<div class="mark-square" style="left:547px;top:713px;width:24px;height:24px"></div>
<h2 class="section-title" style="left:545px;top:748px">About Clearpoint <span>Dental</span> Supply</h2>
<p class="abs about-copy" style="top:801px">Nam libero tempore, cum soluta nobis est eligendi optio cumque nihil impedit quo minus id quod maxime placeat facere possimus, omnis voluptas assumenda est, omnis dolor repellendus. Temporibus autem quibusdam et aut officiis debitis aut rerum necessitatibus saepe eveniet ut et voluptates repudiandae sint et molestiae non recusandae.</p>
<p class="abs about-copy" style="top:976px">Itaque earum rerum hic tenetur a sapiente delectus, ut aut reiciendis voluptatibus maiores alias consequatur aut perferendis doloribus asperiores repellat.</p>
<div class="btn" style="left:545px;top:1051px;width:131px;height:46px">Read More</div>

<!-- areas -->
<div class="abs areas"></div>
<div class="mark-square" style="left:113px;top:1231px;width:24px;height:22px"></div>
<h2 class="section-title" style="left:112px;top:1265px;color:#fff">Areas of Practice</h2>
<div class="rule" style="top:1338px"></div>
<div class="area-img" style="top:1360px;background:linear-gradient(90deg,#3a5f8c,#c59a6a 50%,#4b6d93)" role="img" aria-label="Photo of cardboard boxes moving on a warehouse conveyor"></div>
<p class="area-name" style="top:1391px">Distribution</p>
<p class="area-desc" style="top:1364px">Itaque earum rerum hic tenetur a sapiente delectus, ut aut reicie ndis voluptatibus maiores alias consequatur aut perferendis doloribus asperiores repellat.</p>
<div class="rule" style="top:1469px"></div>
<div class="area-img" style="top:1492px;background:linear-gradient(90deg,#123a5e,#3f8ec4 50%,#1d5584)" role="img" aria-label="Photo of pharmaceutical vials on a production line"></div>
<p class="area-name" style="top:1523px">Pharma</p>
<p class="area-desc" style="top:1495px">Temporibus autem quibusdam et aut officiis debitis aut rerum necessitatibus saepe eveniet ut et voluptates repudiandae sint et molestiae non recusandae.</p>
<div class="rule" style="top:1602px"></div>
<div class="area-img" style="top:1625px;background:linear-gradient(90deg,#c7d6e6,#f1f4f7 50%,#9fb6cf)" role="img" aria-label="Photo of technicians in white coats working in a clean lab"></div>
<p class="area-name" style="top:1656px">Capital Equipment</p>
<p class="area-desc" style="top:1628px">Nam libero tempore, cum soluta nobis est eligendi optio cumque nihil impedit quo minus id quod maxime placeat facere possimusomnis voluptas.,</p>
<div class="rule" style="top:1733px"></div>
<div class="btn" style="left:112px;top:1788px;width:131px;height:44px">View All</div>

<!-- testimonials -->
<div class="mark-square" style="left:588px;top:1971px;width:24px;height:22px"></div>
<h2 class="section-title" style="left:0;width:1200px;text-align:center;top:2006px">What <span>Customer</span> Says</h2>
<div class="card outlined" style="left:103px;top:2088px">
  <div class="stars">★★★★★</div>
  <p class="quote">Temporibus autem quibusdam et aut officiis debitis aut rerum neus saepe facere mus, onis voluptas eveniet ut et voluptates repudae sint et molestiae voluptates repudae sint et molestia enon lorem recusadae.</p>
  <div class="person"><div class="avatar" role="img" aria-label="Customer portrait"></div><div><p class="person-name">Graham Ellison</p><p class="person-loc">United States</p></div></div>
</div>
<div class="card raised" style="left:446px;top:2128px">
  <div class="stars">★★★★★</div>
  <p class="quote">Itaque earum rerum hic tenetur a sapiene delectus, ut aut reicieis aut perferndis doloribus asperiores volupatibus maiores alias conse uatur aut perferndis doloribus asperiores reiciendis voluptatbus repellat</p>
  <div class="person"><div class="avatar" style="border:2px solid var(--accent);background:linear-gradient(135deg,#e6c6a8,#9a6a48)" role="img" aria-label="Customer portrait"></div><div><p class="person-name">Noreen</p><p class="person-loc">United States</p></div></div>
</div>
<div class="card outlined" style="left:785px;top:2088px">
  <div class="stars">★★★★★</div>
  <p class="quote">At vero eos et accusamus et iusto odio dignissimos ducimus qui aut perfer ndis doloribus asperi blaiis praese ntium volupttum deleniti atque corrpi quos dolores et quas occaecati cupie non provident.</p>
  <div class="person"><div class="avatar" style="background:linear-gradient(135deg,#7e8a8c,#3f4a4c)" role="img" aria-label="Customer portrait"></div><div><p class="person-name">Martin Hale</p><p class="person-loc">United States</p></div></div>
</div>

<!-- contact -->
<div class="abs contact"></div>
<div class="mark-square" style="left:588px;top:2615px;width:24px;height:22px"></div>
<h2 class="section-title" style="left:0;width:1200px;text-align:center;top:2650px">Get In <span>Touch With</span> Us</h2>
<div class="field" style="left:113px;top:2730px;width:468px;height:59px">Name</div>
<div class="field" style="left:618px;top:2730px;width:469px;height:59px">Email</div>
<div class="field" style="left:113px;top:2806px;width:468px;height:59px">Phone Number</div>
<div class="field" style="left:618px;top:2806px;width:469px;height:59px">Address</div>
<div class="field area" style="left:113px;top:2886px;width:977px;height:159px">Message</div>
<div class="btn" style="left:533px;top:3105px;width:133px;height:46px">Submit</div>

<!-- footer -->
<div class="abs footer-arc"></div>
<div class="abs footer"></div>
<div class="abs foot-brand"><span class="mark-square"></span><p>ClearpointDentalSupply</p></div>

<p class="abs foot-head" style="left:429px">Quick Links</p>
<ul class="abs foot-list" style="left:429px;top:3382px">
  <li><svg width="14" height="12" viewBox="0 0 14 12"><path d="M0 6h11M7 1l5 5-5 5" stroke="#fff" stroke-width="2.2" fill="none"/></svg>Home</li>
  <li><svg width="14" height="12" viewBox="0 0 14 12"><path d="M0 6h11M7 1l5 5-5 5" stroke="#fff" stroke-width="2.2" fill="none"/></svg>About</li>
  <li><svg width="14" height="12" viewBox="0 0 14 12"><path d="M0 6h11M7 1l5 5-5 5" stroke="#fff" stroke-width="2.2" fill="none"/></svg>Areas of Practice</li>
  <li><svg width="14" height="12" viewBox="0 0 14 12"><path d="M0 6h11M7 1l5 5-5 5" stroke="#fff" stroke-width="2.2" fill="none"/></svg>Testimonials</li>
  <li><svg width="14" height="12" viewBox="0 0 14 12"><path d="M0 6h11M7 1l5 5-5 5" stroke="#fff" stroke-width="2.2" fill="none"/></svg>Contact Us</li>
</ul>

<p class="abs foot-head" style="left:662px">Help Links</p>
<ul class="abs foot-list" style="left:662px;top:3382px">
  <li><svg width="14" height="12" viewBox="0 0 14 12"><path d="M0 6h11M7 1l5 5-5 5" stroke="#fff" stroke-width="2.2" fill="none"/></svg>FAQ</li>
  <li><svg width="14" height="12" viewBox="0 0 14 12"><path d="M0 6h11M7 1l5 5-5 5" stroke="#fff" stroke-width="2.2" fill="none"/></svg>Terms of use</li>
  <li><svg width="14" height="12" viewBox="0 0 14 12"><path d="M0 6h11M7 1l5 5-5 5" stroke="#fff" stroke-width="2.2" fill="none"/></svg>Privacy Policy</li>
  <li><svg width="14" height="12" viewBox="0 0 14 12"><path d="M0 6h11M7 1l5 5-5 5" stroke="#fff" stroke-width="2.2" fill="none"/></svg>Support Links</li>
  <li><svg width="14" height="12" viewBox="0 0 14 12"><path d="M0 6h11M7 1l5 5-5 5" stroke="#fff" stroke-width="2.2" fill="none"/></svg>Conditions</li>
</ul>

<p class="abs foot-head" style="left:886px">Contact Us</p>
<div class="ic" style="left:886px;top:3390px"><svg width="14" height="18" viewBox="0 0 14 18"><path d="M7 0C3 0 0 3 0 7c0 5 7 11 7 11s7-6 7-11c0-4-3-7-7-7z" fill="#fff"/><circle cx="7" cy="7" r="2.6" fill="#10a8e8"/></svg></div>
<p class="abs foot-contact" style="left:931px;top:3386px">Clearpoint Dental Supply<br>United States</p>
<div class="ic" style="left:886px;top:3455px"><svg width="16" height="16" viewBox="0 0 16 16"><path d="M3 1l3 3-2 2c1 2 3 4 5 5l2-2 3 3-2 3C7 15 1 9 0 3z" fill="#fff"/></svg></div>
<p class="abs foot-contact" style="left:931px;top:3454px">+1 800 555 0142</p>
<div class="ic" style="left:886px;top:3517px"><svg width="16" height="12" viewBox="0 0 16 12"><rect width="16" height="12" rx="1.5" fill="#fff"/><path d="M1 1l7 6 7-6" stroke="#10a8e8" stroke-width="1.6" fill="none"/></svg></div>
<p class="abs foot-contact" style="left:931px;top:3516px">info@clearpointdental.com</p>

<div class="abs foot-rule"></div>
<p class="abs copy">Copyrights@2023. Clearpoint Dental Supply.All Rights Reserved</p>
<span class="social" style="left:917px"></span>
<span class="social" style="left:965px"></span>
<span class="social" style="left:1014px"></span>
<span class="social" style="left:1061px"></span>

</body>
</html>
```